Client Meeting and installation Email Follow up

I would like a follow-up email template created.
Currently, we do a lot of new construction builds and meet with clients about 6-3 months before they take possession of their new house. I want a follow-up email template to be sent after the homeowner takes possession of their house that enquires if the clients are happy about their new lighting, the service they received, and their customer service representative with Brightwell Lamps and Breezes. I have attached a few files of what our current marketing looks like.
Target Market(s)
Home Owners We have already met with
Industry/Entity Type
Residential lighting
Font styles to use
Other font styles liked:
- Alta Light, Playfair Display, Montserrat
Colors
Designer to choose colors to be used in the design.
Look and feel
Each slider illustrates characteristics of the customer's brand and the style your logo design should communicate.

```html
<!DOCTYPE html>
<html lang="en">
<head>
<meta charset="utf-8">
<title>Brightwell Lamps and Breezes – Thank You</title>
<link href="https://fonts.googleapis.com/css2?family=Marcellus&family=Poppins:wght@300;400;600&display=swap" rel="stylesheet">
<style>
  :root {
    --ink: #2b2b2b;
    --text: #3d3d3d;
    --accent: #a27b62;
    --button: #9b7b67;
    --hero-bg: #f1f1f1;
    --marble: #efefef;
    --white: #ffffff;
    --muted: #777777;
  }
  * { margin: 0; padding: 0; box-sizing: border-box; }
  html, body { width: 1200px; height: 4642px; overflow: hidden; background: var(--white); }
  body { position: relative; font-family: "Poppins", sans-serif; color: var(--text); }
  .abs { position: absolute; }
  .serif { font-family: "Marcellus", serif; color: var(--ink); font-weight: 400; }

  .hero { left: 0; top: 0; width: 1200px; height: 982px; background: linear-gradient(180deg, #f6f6f6 0%, #ececec 70%, #e6e6e6 100%); }
  .brand { font-family: "Marcellus", serif; color: #111; text-align: center; line-height: 1; }
  .brand-top { left: 373px; top: 108px; width: 452px; font-size: 64px; letter-spacing: 2px; }
  .brand-bottom { left: 373px; top: 188px; width: 452px; font-size: 40px; letter-spacing: 1px; }
  .hero-title { left: 0; top: 368px; width: 1200px; text-align: center; font-size: 82px; line-height: 102px; }
  .rule { height: 4px; background: var(--accent); }
  .hero-rule { left: 524px; top: 580px; width: 153px; }
  .ph { position: absolute; }
  .pendant { left: 68px; top: 0; width: 200px; height: 333px; background: linear-gradient(180deg, #6a6a6a, #9a9a9a); opacity: .55; }
  .living { left: 54px; top: 600px; width: 1100px; height: 436px; background: linear-gradient(180deg, #e6e6e6 0%, #c9c9c9 55%, #b9b2a5 100%); }

  .intro-title { left: 68px; top: 1180px; font-size: 68px; line-height: 76px; }
  .intro-rule { left: 68px; top: 1362px; width: 152px; }
  .intro-text { left: 68px; top: 1396px; width: 540px; font-size: 30px; line-height: 54px; font-weight: 300; }
  .nightstand { left: 720px; top: 1108px; width: 395px; height: 694px; background: linear-gradient(180deg, #f2ede4 0%, #d9b98a 60%, #c79b66 100%); }

  .marble { left: 0; top: 1778px; width: 1200px; height: 1262px; background: linear-gradient(160deg, #f3f3f3, #e9e9e9); }
  .exp-title { left: 0; top: 1888px; width: 1200px; text-align: center; font-size: 68px; line-height: 76px; }
  .exp-rule { left: 524px; top: 2065px; width: 153px; }
  .question { left: 0; width: 1200px; text-align: center; font-size: 30px; font-weight: 300; }
  .dot { width: 11px; height: 11px; border-radius: 50%; background: var(--accent); left: 595px; }
  .btn { left: 423px; width: 355px; height: 76px; background: var(--button); color: var(--white); font-weight: 600; font-size: 30px; display: flex; align-items: center; justify-content: center; text-decoration: none; }

  .photo-1 { left: 68px; top: 2578px; width: 409px; height: 517px; background: linear-gradient(180deg, #efe9e6, #c9a88c); }
  .photo-2 { left: 515px; top: 2688px; width: 618px; height: 517px; background: linear-gradient(180deg, #ece6df, #b79a7a 75%, #3f5147); }
  .photo-3 { left: 68px; top: 3124px; width: 409px; height: 438px; background: linear-gradient(180deg, #3c3c3c 0%, #f2f2f2 25%, #8a7564 100%); }
  .photo-4 { left: 519px; top: 3243px; width: 290px; height: 440px; background: linear-gradient(180deg, #f0f0f0, #d8d8d8 70%, #6f6f6f); }
  .photo-5 { left: 841px; top: 3243px; width: 292px; height: 440px; background: linear-gradient(180deg, #efe7da, #5e7a62 60%, #8a5a3a); }

  .closing { left: 150px; top: 3808px; width: 900px; text-align: center; font-size: 30px; line-height: 50px; font-weight: 300; }

  .footer { left: 0; top: 4182px; width: 1200px; height: 460px; background: linear-gradient(160deg, #f1f1f1, #e8e8e8); }
  .foot-brand-top { left: 400px; top: 4262px; width: 400px; font-size: 40px; letter-spacing: 1px; }
  .foot-brand-bottom { left: 400px; top: 4312px; width: 400px; font-size: 24px; }
  .social { left: 436px; top: 4389px; }
  .links { left: 0; top: 4482px; width: 1200px; text-align: center; font-size: 25px; font-weight: 300; color: var(--text); word-spacing: 4px; }
  .links span { margin: 0 28px; }
  .copyright { left: 0; top: 4544px; width: 1200px; text-align: center; font-size: 25px; font-weight: 300; }
  .code { right: 22px; top: 4518px; font-size: 20px; color: var(--muted); }
</style>
</head>
<body>
  <section class="abs hero"></section>
  <div class="ph pendant" role="img" aria-label="Black cube pendant light hanging from the ceiling"></div>
  <div class="abs brand brand-top">BRIGHTWELL</div>
  <div class="abs brand brand-bottom">LAMPS &amp; BREEZES</div>
  <h1 class="abs serif hero-title">THANK YOU FOR<br>CHOOSING US</h1>
  <div class="abs rule hero-rule"></div>
  <div class="ph living" role="img" aria-label="Grey sofa with green throw, potted plant and tripod floor lamp"></div>

  <h2 class="abs serif intro-title">HOW DO YOU<br>LIKE IT ?</h2>
  <div class="abs rule intro-rule"></div>
  <p class="abs intro-text">We hope you're enjoying your new home and its stunning lighting from Brightwell Lamps and Breezes. Now that you've had time to settle in, we'd love to hear your thoughts.</p>
  <div class="ph nightstand" role="img" aria-label="Rattan nightstand with books and a brass globe table lamp"></div>

  <section class="abs marble"></section>
  <h2 class="abs serif exp-title">TELL US ABOUT YOUR<br>EXPERIENCE</h2>
  <div class="abs rule exp-rule"></div>
  <p class="abs question" style="top:2106px">Are you satisfied with the lighting installation?</p>
  <div class="abs dot" style="top:2170px"></div>
  <p class="abs question" style="top:2196px">How was the service you received?</p>
  <div class="abs dot" style="top:2258px"></div>
  <p class="abs question" style="top:2288px">How did your customer service representative do?</p>
  <a class="abs btn" style="top:2396px" href="#">Provide Feedback</a>

  <div class="ph photo-1" role="img" aria-label="Wooden candle chandelier in a bright room"></div>
  <div class="ph photo-2" role="img" aria-label="Bedroom with a ceiling fan, dresser and upholstered bed"></div>
  <div class="ph photo-3" role="img" aria-label="Dining room with an iron chandelier above a wooden table"></div>
  <div class="ph photo-4" role="img" aria-label="Modern linear pendant lights above a grey sofa"></div>
  <div class="ph photo-5" role="img" aria-label="Kitchen with green cabinets and a brass globe chandelier"></div>

  <p class="abs closing">Your feedback helps us to serve you better. Please don’t hesitate to share your thoughts or get in touch if you have any questions.</p>
  <a class="abs btn" style="top:4027px" href="#">Provide Feedback</a>

  <footer class="abs footer"></footer>
  <div class="abs brand foot-brand-top">BRIGHTWELL</div>
  <div class="abs brand foot-brand-bottom">LAMPS &amp; BREEZES</div>
  <svg class="abs social" width="328" height="56" viewBox="0 0 328 56" role="img" aria-label="Social media links">
    <g fill="none" stroke="#2b2b2b" stroke-width="2">
      <circle cx="27" cy="28" r="26"/>
      <circle cx="95" cy="28" r="26"/>
      <circle cx="162" cy="28" r="26"/>
      <circle cx="231" cy="28" r="26"/>
      <circle cx="299" cy="28" r="26"/>
    </g>
  </svg>
  <p class="abs links">Locations<span>|</span>Contact Us<span>|</span>Privacy<span>|</span>Unsubscribe</p>
  <p class="abs copyright">© Brightwell Lamps and Breezes. All Rights Reserved.</p>
  <p class="abs code">C50</p>
</body>
</html>
```